Black Granite Web Design Project

We are looking for a design for a new company that will be selling Black Granite slabs and tiles. We will be selling to both end-consumers and granite installers. We have already settled on a logo and hopefully this will give an idea of what we like in our designs. We are not going to be selling online but want people to call us so the site is basically an enhanced business card. We will be focusing a lot on SEO so the design will have to keep that in mind.

We would like to keep the design in 1024x768 to make it easily view-able on all devices.

Regarding navigation there should only be a few sub-pages, like "Granite Slabs", "Granite Tiles", "Delivery", "Contact"

Aside from that we are open to designs. One idea we did have was to personalize the site and have a person there somehow to represent the company, making the user feel there are real people behind this site. This is just an idea and not a must.

The name of the company and site is "Copper Ridge Marmora"

Thanks
Updates

Hello All,

Thanks for the great designs. There are some good looking designs that show beautiful kitchens but this site is made for the granite installers and not the retail consumers. So in order not to to confuse the buyers I would like to keep this as much about the raw products as possible. The raw products being the granite slabs, thereby making it obvious we don't sell granite counter tops. 

This design will really be the identity of this company so it is important we get the right message across on this index page and that this page is as complete as possible.

Again, thanks for all the work being put into this.

Target Market(s)

The target audience is granite installers or companies that would with granite slabs.

Industry/Entity Type

Business

```html
<!DOCTYPE html>
<html lang="en">
<head>
<meta charset="utf-8">
<title>Copper Ridge Marmora</title>
<link href="https://fonts.googleapis.com/css2?family=Arimo:wght@400;700&display=swap" rel="stylesheet">
<style>
:root{
  --ink:#1b1b1b;
  --text:#555555;
  --white:#ffffff;
  --band:#d3d2cc;
  --footer:#eeeeee;
  --bar:#1d1d1d;
  --green:#3a9a1c;
  --field:#353331;
  --rule:#d8d8d8;
  --muted:#9a9a9a;
}
*{margin:0;padding:0;box-sizing:border-box}
html,body{width:884px;height:1200px;overflow:hidden}
body{position:relative;background:var(--white);font-family:"Arimo",Arial,sans-serif;color:var(--ink)}
.abs{position:absolute}
h2,h3{font-weight:400}

/* hero */
.hero{left:0;top:0;width:884px;height:383px;background:linear-gradient(160deg,#8a857c 0%,#b9b3a8 35%,#7b776f 60%,#a29c91 80%,#5d5a53 100%)}
.dots{right:12px;top:362px;display:flex;gap:7px}
.dots span{width:9px;height:9px;border-radius:50%;background:var(--white)}

/* header */
.header{left:71px;top:0;width:736px;height:73px;background:var(--white);box-shadow:0 2px 8px rgba(0,0,0,.3)}
.brand{left:16px;top:25px;display:flex;align-items:center;gap:8px;white-space:nowrap}
.brand-mark{width:22px;height:22px;background:var(--ink)}
.brand-name{font-weight:700;font-size:13px;color:var(--ink);letter-spacing:0}
.nav{right:8px;top:26px;display:flex;font-size:10px;white-space:nowrap}
.nav a{color:var(--ink);text-decoration:none;padding:6px 7px;margin-left:4px;height:21px;line-height:10px}
.nav a.active{background:var(--ink);color:var(--white);padding:6px 13px;font-weight:700}

/* welcome */
.welcome-title{left:70px;top:403px;font-size:12px;color:var(--ink)}
.welcome-title b{font-weight:700}
.welcome-photo{left:71px;top:425px;width:202px;height:103px;background:linear-gradient(120deg,#2f4a1c,#7fa13e 45%,#c9d98c 70%,#5c7a29)}
.welcome-copy{left:285px;top:424px;width:273px;font-size:9px;line-height:14px;color:var(--text)}
.more{left:285px;top:505px;font-size:10px;font-weight:700;color:var(--ink)}

.why-title{left:586px;top:409px;font-size:12px;color:var(--ink)}
.why-list{left:589px;top:428px;width:204px;list-style:none}
.why-list li{position:relative;padding:3px 0 4px 18px;border-bottom:1px solid var(--rule);margin-bottom:6px}
.why-list li:last-child{border-bottom:none}
.why-list svg{position:absolute;left:0;top:3px}
.why-list h3{font-size:8.5px;font-weight:700;color:var(--ink);margin-bottom:2px;white-space:nowrap}
.why-list p{font-size:9px;line-height:12px;color:var(--text)}

/* products */
.products{left:0;top:599px;width:884px;height:355px;background:var(--band)}
.products-title{left:0;top:619px;width:884px;text-align:center;font-size:13px;color:var(--ink);font-weight:700;letter-spacing:.3px}
.card{top:658px;width:201px;height:255px;background:var(--white);text-align:center}
.card-img{width:100%;height:137px}
.card h3{font-size:11px;font-weight:400;margin-top:15px;letter-spacing:.2px}
.card p{font-size:9px;line-height:13px;color:var(--text);padding:0 16px;margin-top:11px}
.card .read{position:absolute;left:0;right:0;top:235px;font-size:9px;color:var(--green)}
.card .read b{color:var(--ink);margin-left:4px}

/* footer */
.footer{left:0;top:954px;width:884px;height:204px;background:var(--footer)}
.f-title{top:980px;font-size:11px;color:var(--ink);letter-spacing:.3px}
.f-list{list-style:none;font-size:9px;line-height:18.5px;color:var(--ink)}
.f-list .current{color:var(--green)}
.field{background:var(--field);border-radius:3px;color:#dcdcdc;font-size:8px;padding:9px 8px;box-shadow:0 1px 2px rgba(0,0,0,.3)}
.submit{left:739px;top:1109px;font-size:11px;font-weight:700;color:var(--ink)}

.bar{left:0;top:1158px;width:884px;height:42px;background:var(--bar)}
.legal{left:97px;top:1167px;font-size:9px;line-height:11px;color:var(--muted);letter-spacing:.2px}
.social{left:673px;top:1166px;display:flex;gap:4px}
.social span{width:23px;height:23px;border-radius:50%;border:1px solid #777}
</style>
</head>
<body>

<div class="abs hero" role="img" aria-label="Photograph of a large weathered granite rock face"></div>
<div class="abs dots"><span></span><span></span><span></span><span></span></div>

<header class="abs header">
  <div class="abs brand"><span class="brand-mark"></span><span class="brand-name">COPPER RIDGE MARMORA</span></div>
  <nav class="abs nav">
    <a class="active">HOME</a><a>ABOUT US</a><a>GRANITE SLABS</a><a>GRANITE TILES</a><a>DELIVERY</a><a>CONTACT</a>
  </nav>
</header>

<h2 class="abs welcome-title">WELCOME TO <b>COPPER RIDGE MARMORA</b></h2>
<div class="abs welcome-photo" role="img" aria-label="Photograph of a person outdoors in a green field"></div>
<p class="abs welcome-copy">Sed ut perspiciatis unde omnis iste natus error sit voluptatem accus antium doloremque laudantium, totam rem eaque ipsa quae ab illo inventore veritatis et quasi architecto beatae vitae dicta sunt explica bo. Nemo enim ipvoluptatem quia voluptas sit aspernatur aut odit aut fugit</p>
<a class="abs more">Know more about us</a>

<h2 class="abs why-title">WHY CHOOSE US</h2>
<ul class="abs why-list">
  <li><svg width="11" height="10" viewBox="0 0 11 10"><path d="M1 5l3 3 6-7" fill="none" stroke="#8a8a8a" stroke-width="2"/></svg><h3>OVER 30 YEARS OF PROVEN EXPERIENCE</h3><p>Lorem ipsum dolor sit amet, consectetuer scing elit, sed diam nonummy nibh...</p></li>
  <li><svg width="11" height="10" viewBox="0 0 11 10"><path d="M1 5l3 3 6-7" fill="none" stroke="#8a8a8a" stroke-width="2"/></svg><h3>CERTIFIED BY GOVT AGENCIES</h3><p>Lorem ipsum dolor sit amet, consectetuer scing elit, sed diam nonummy nibh...</p></li>
  <li><svg width="11" height="10" viewBox="0 0 11 10"><path d="M1 5l3 3 6-7" fill="none" stroke="#8a8a8a" stroke-width="2"/></svg><h3>PROVEN AND TESTED EVERYWHERE</h3><p>Lorem ipsum dolor sit amet, consectetuer scing elit, sed diam nonummy nibh...</p></li>
</ul>

<section class="abs products"></section>
<h2 class="abs products-title">OUR TOP RANGE PRODUCTS</h2>

<article class="abs card" style="left:105px">
  <div class="card-img" role="img" aria-label="Close-up of speckled pink and black granite" style="background:linear-gradient(135deg,#6b5a55,#a07f75 40%,#3d3634 70%,#8d756d)"></div>
  <h3>GRANITE PRE FABS</h3>
  <p>Sed ut perspiciatis unde omnis iste natus error sit voluptatem accusantium doloremq ue laudantium, totam rem eaque ipsa quae ab illo inventore veritatis</p>
  <div class="read">Read more<b>»</b></div>
</article>
<article class="abs card" style="left:343px">
  <div class="card-img" role="img" aria-label="Close-up of a veined beige and brown granite slab" style="background:linear-gradient(135deg,#8a7a5c,#c9b893 40%,#9c7b52 65%,#6e6a55)"></div>
  <h3>GRANITE RAW SLABS</h3>
  <p>Sed ut perspiciatis unde omnis iste natus error sit voluptatem accusantium doloremq ue laudantium, totam rem eaque ipsa quae ab illo inventore veritatis</p>
  <div class="read">Read more<b>»</b></div>
</article>
<article class="abs card" style="left:574px">
  <div class="card-img" role="img" aria-label="Grid of granite tile samples in gold, brown, blue and red" style="background:linear-gradient(180deg,#9a7552 0%,#7a5e4d 50%,#4f6e9a 51%,#8f6660 75%,#2f4f7e 100%)"></div>
  <h3>GRANITE TILES</h3>
  <p>Sed ut perspiciatis unde omnis iste natus error sit voluptatem accusantium doloremq ue laudantium, totam rem eaque ipsa quae ab illo inventore veritatis</p>
  <div class="read">Read more<b>»</b></div>
</article>

<footer class="abs footer"></footer>
<h2 class="abs f-title" style="left:97px">NAVIGATION</h2>
<ul class="abs f-list" style="left:98px;top:1004px">
  <li class="current">Home</li><li>About Us</li><li>Granite Slabs</li><li>Granite Tiles</li><li>Delvery</li><li>Contact</li>
</ul>
<h2 class="abs f-title" style="left:245px">OUR ASSOCIATIONS</h2>
<ul class="abs f-list" style="left:246px;top:1003px">
  <li>Sed ut perspiciatis unde omnis iste natus</li><li>Suae ab illo inventore veritatis</li><li>Sed ut perspiciatis unde</li><li>Suae ab illo inventore veritatis</li><li>Sed ut perspiciatis unde omnis</li><li>Suae ab illo invento</li>
</ul>
<h2 class="abs f-title" style="left:447px;top:979px">CONTACTS</h2>
<div class="abs field" style="left:450px;top:1005px;width:155px;height:28px">Name</div>
<div class="abs field" style="left:450px;top:1040px;width:155px;height:28px">Email</div>
<div class="abs field" style="left:450px;top:1075px;width:155px;height:28px">Website</div>
<div class="abs field" style="left:621px;top:1005px;width:156px;height:99px">Message</div>
<div class="abs submit">Submit</div>

<div class="abs bar"></div>
<div class="abs legal">COPYRIGHT 2013. ALL RIGHTS RESERVED.<br>TERMS &amp; CONDITIONS &nbsp;- &nbsp;PRIVACY &nbsp;- &nbsp;DISCLAIMER</div>
<div class="abs social">
  <span style="background:#d9531e"></span><span style="background:#c0392b"></span><span style="background:#3b5998"></span><span style="background:#2ea1d8"></span>
</div>

</body>
</html>
```